Schriftdesign für Shop-Header Bild (Schmuckhandel) / Online-Marketing Material
Wir verkaufen Schmuck im Onlineshop mit Herz
Wir benötigen den vorgegebenen Text in schöner Form, Farbe und Größe harmonisch eingefügt, in unserem Bild.
Folgender Text soll sich schick ins Bild einfügen oder in 3-D vielleicht in Schriftfarbe gold hervorheben:
Mit ganzem Herzen für Sie da!
Ihr Online -Juwelier mit Herz
Siehe auch unser altes Bild mit Text, im Shop, wie es nicht aussehen sollte: www.sonnenflocke.de

```html
<!DOCTYPE html>
<html lang="de">
<head>
<meta charset="utf-8">
<title>Mit ganzem Herzen – Shop-Header</title>
<link rel="stylesheet" href="https://fonts.googleapis.com/css2?family=Mr+Dafoe&family=Oswald:wght@200;300&display=swap">
<style>
  :root {
    --page-bg: #ffffff;
    --silk-light: #b48a80;
    --silk-mid: #8a5f55;
    --silk-deep: #5e3a31;
    --band-dark: #1c0f0c;
    --type-light: #f8f1ec;
    --type-soft: #ecd6cb;
  }
  html, body {
    margin: 0;
    padding: 0;
    width: 1200px;
    height: 1200px;
    overflow: hidden;
    background: var(--page-bg);
  }
  .header-banner {
    position: absolute;
    left: 60px;
    top: 465px;
    width: 1080px;
    height: 270px;
    overflow: hidden;
    background: var(--silk-deep);
  }
  .header-banner__photo {
    position: absolute;
    inset: 0;
    background:
      radial-gradient(ellipse 420px 200px at 300px 110px, var(--silk-light), transparent 75%),
      radial-gradient(ellipse 180px 220px at 1010px 110px, #8c6762, transparent 80%),
      linear-gradient(90deg, var(--silk-mid) 0%, #7a5047 45%, var(--silk-deep) 70%, #6e4a44 100%);
  }
  .header-banner__band {
    position: absolute;
    left: 0;
    right: 0;
    bottom: 0;
    height: 78px;
    background: linear-gradient(180deg, rgba(28,15,12,0) 0%, var(--band-dark) 28%, var(--band-dark) 100%);
  }
  .header-banner__type {
    position: absolute;
    inset: 0;
    width: 1080px;
    height: 270px;
  }
  .headline__kicker {
    font-family: "Oswald", sans-serif;
    font-weight: 200;
    font-size: 38px;
    fill: var(--type-soft);
  }
  .headline__script {
    font-family: "Mr Dafoe", cursive;
    font-weight: 400;
    font-size: 112px;
    fill: var(--type-light);
  }
  .headline__closing {
    font-family: "Oswald", sans-serif;
    font-weight: 200;
    font-size: 54px;
    fill: var(--type-soft);
  }
  .tagline {
    font-family: "Oswald", sans-serif;
    font-weight: 300;
    font-size: 17px;
    fill: var(--type-light);
  }
</style>
</head>
<body>
  <section class="header-banner">
    <div class="header-banner__photo" role="img" aria-label="Goldener Herzanhänger an feiner Kette auf altrosa Seidenstoff"></div>
    <div class="header-banner__band"></div>
    <svg class="header-banner__type" viewBox="0 0 1080 270" xmlns="http://www.w3.org/2000/svg">
      <text class="headline__kicker" x="687" y="73" textLength="156" lengthAdjust="spacingAndGlyphs">MIT GANZEM</text>
      <text class="headline__script" x="538" y="126" textLength="278" lengthAdjust="spacingAndGlyphs">Herzen</text>
      <text class="headline__closing" x="583" y="184" textLength="157" lengthAdjust="spacingAndGlyphs">für Sie da!</text>
      <text class="tagline" x="350" y="245" textLength="381" lengthAdjust="spacing">IHR ONLINE-JUWELIER MIT HERZ</text>
    </svg>
  </section>
</body>
</html>
```